Website Design for R W Builders: Showcasing Excellence in General Contracting

R W Builders, a leading general contractor based in California, is seeking a professional and engaging website design to effectively showcase our expertise, services, and commitment to excellence. The website will serve as a digital platform to represent our brand identity, highlight our portfolio, and attract potential clients in various sectors.

Key Objectives:

Reflect Company Identity: The website should accurately reflect the identity and values of R W Builders, including our dedication to quality, professionalism, and client satisfaction.
Showcase Services: Highlight our wide range of general contracting services, including but not limited to construction management, design-build, renovation, and commercial construction.
Portfolio Display: Display an extensive portfolio of past projects completed by R W Builders, showcasing our capabilities, craftsmanship, and successful outcomes.
Client Testimonials: Incorporate client testimonials and case studies to demonstrate our track record of delivering projects on time, within budget, and to the highest standards.
Contact Information: Ensure easy access to contact information, including phone number, email, and physical address, to facilitate communication with potential clients.
Responsive Design: Develop a responsive website design optimized for various devices and screen sizes, ensuring a seamless user experience across desktops, laptops, tablets, and smartphones.
Search Engine Optimization (SEO): Implement SEO best practices to enhance the visibility of the website on search engines, increasing organic traffic and generating leads.
User-Friendly Navigation: Create an intuitive and user-friendly navigation structure that enables visitors to easily find the information they need, such as services, portfolio, testimonials, and contact details.
Visual Appeal: Utilize visually appealing graphics, images, and layout designs to capture the attention of visitors and leave a lasting impression of professionalism and quality.
Compliance and Security: Ensure compliance with industry standards and regulations, as well as implementing necessary security measures to protect user data and privacy.

```html
<!DOCTYPE html>
<html lang="en">
<head>
<meta charset="utf-8">
<title>R W Builders — General Contracting</title>
<link href="https://fonts.googleapis.com/css2?family=Oswald:wght@500;600;700&family=Poppins:wght@300;400;500;600&family=Raleway:wght@400;500&display=swap" rel="stylesheet">
<style>
:root{
  --navy:#1b3272;
  --navy-deep:#1f3d7e;
  --cyan:#0aa7e0;
  --ink:#222;
  --body:#444;
  --grey-bg:#f3f3f3;
  --footer:#1d1d1d;
  --white:#fff;
}
*{margin:0;padding:0;box-sizing:border-box}
html,body{width:1200px;height:3879px;overflow:hidden;background:var(--white)}
body{position:relative;font-family:'Poppins',sans-serif;color:var(--ink)}
.abs{position:absolute}
.display{font-family:'Oswald',sans-serif;font-weight:600;text-transform:uppercase;letter-spacing:.3px}
.btn{position:absolute;display:flex;align-items:center;justify-content:center;background:var(--cyan);color:var(--white);font-family:'Oswald',sans-serif;font-weight:500;text-transform:uppercase;font-size:15px;border-radius:3px}

/* header */
.brand{left:136px;top:40px;font-family:'Oswald',sans-serif;font-weight:700;font-size:28px;color:var(--ink);display:flex;align-items:center;gap:10px;text-transform:uppercase}
.brand-mark{width:22px;height:22px;background:var(--ink)}
.topbar{left:340px;top:0;width:860px;height:57px;background:var(--navy);border-bottom-left-radius:28px;color:var(--white);font-family:'Oswald',sans-serif;font-weight:500;font-size:19px}
.topbar .item{position:absolute;top:14px;display:flex;align-items:center;gap:14px}
.topbar .sep{position:absolute;left:247px;top:12px;width:1px;height:33px;background:rgba(255,255,255,.45)}
.social{position:absolute;top:7px;width:43px;height:43px;border-radius:50%;background:var(--cyan)}
.nav{top:97px;font-family:'Raleway',sans-serif;font-size:15px;color:#333}
.login{left:986px;top:84px;width:103px;height:44px}

/* hero */
.hero{left:0;top:151px;width:1200px;height:599px;background:linear-gradient(120deg,#3b3a36 0%,#6e5e48 35%,#c49a5e 62%,#8a6a44 80%,#2f2a26 100%)}
.hero h1{position:absolute;left:113px;top:143px;font-family:'Oswald',sans-serif;font-weight:700;font-size:62px;line-height:77px;color:var(--white);text-transform:uppercase}
.hero .cta{left:113px;top:400px;width:110px;height:44px}
.dot{position:absolute;width:13px;height:13px;border-radius:50%;background:var(--white)}

/* services */
.section-title{position:absolute;left:0;width:1200px;text-align:center;font-family:'Oswald',sans-serif;font-weight:600;font-size:38px;color:var(--ink);text-transform:uppercase}
.tab{position:absolute;top:903px;height:44px;display:flex;align-items:center;justify-content:center;font-family:'Oswald',sans-serif;font-weight:500;font-size:15px;text-transform:uppercase;border-radius:2px}
.tab.on{left:417px;width:172px;background:var(--cyan);color:var(--white)}
.tab.off{left:604px;width:179px;border:2px solid var(--cyan);color:var(--ink)}
.card{position:absolute;top:995px;width:232px;height:312px;background:var(--white);box-shadow:0 2px 12px rgba(0,0,0,.1);text-align:center}
.card .icon{position:absolute;left:68px;top:26px;width:96px;height:96px;border-radius:50%;background:var(--cyan);display:flex;align-items:center;justify-content:center}
.card h3{position:absolute;left:0;right:0;top:144px;font-weight:500;font-size:20px}
.card p{position:absolute;left:18px;right:18px;top:180px;font-size:13.5px;line-height:26px;color:var(--body);font-weight:300}
.card .more{position:absolute;left:0;right:0;top:274px;font-size:14px;font-weight:500;color:var(--cyan)}
.card.active{background:var(--navy)}
.card.active h3,.card.active p,.card.active .more{color:var(--white)}
.card.active .icon{background:var(--white)}

/* about */
.about{left:0;top:1412px;width:600px;height:470px;background:var(--grey-bg)}
.about-photo{left:600px;top:1412px;width:600px;height:470px;background:linear-gradient(180deg,#cfd6dc 0%,#b8c2ca 45%,#c78d58 75%,#b06c38 100%)}
.about h2{position:absolute;left:111px;top:52px;font-family:'Oswald',sans-serif;font-weight:600;font-size:36px;text-transform:uppercase}
.about p{position:absolute;left:111px;top:120px;width:428px;font-size:14.5px;line-height:25.6px;color:var(--body);text-align:justify;font-weight:300}
.about .cta{left:111px;top:359px;width:134px;height:51px}

/* testimonials */
.quote{position:absolute;top:2052px;width:80px;height:80px;border-radius:50%;background:var(--navy)}
.quote span{position:absolute;left:16px;top:-2px;font-family:'Oswald',sans-serif;font-weight:700;font-size:78px;color:var(--white);line-height:1}
.testi{position:absolute;top:2101px;width:378px;font-size:14.5px;line-height:25.6px;color:var(--body);text-align:justify;font-weight:300}
.avatar{position:absolute;top:2328px;width:82px;height:82px;border-radius:50%;background:linear-gradient(160deg,#d9dde3,#3c4f72)}
.who{position:absolute;top:2356px;font-size:19px;color:var(--cyan)}
.gdot{position:absolute;top:2453px;width:13px;height:13px;border-radius:50%;background:#ddd}

/* projects */
.projects{left:0;top:2560px;width:1200px;height:922px;background:var(--navy-deep)}
.tile{position:absolute}
.feature{background:linear-gradient(135deg,#2ba6d8,#1c8fc6);display:flex;flex-direction:column;align-items:center;justify-content:center;color:var(--white);text-align:center}
.feature h4{font-family:'Oswald',sans-serif;font-weight:500;font-size:29px;line-height:41px}
.feature p{font-size:14px;line-height:26px;margin-top:12px;font-weight:300}

/* footer */
.footer{left:0;top:3482px;width:1200px;height:397px;background:var(--footer);color:var(--white)}
.footer h5{position:absolute;top:64px;font-size:19.5px;font-weight:500}
.footer ul{position:absolute;top:104px;list-style:none;font-size:14.5px;line-height:25.6px;font-family:'Raleway',sans-serif}
.footer li::before{content:"»";margin-right:12px}
.contact-row{position:absolute;left:864px;display:flex;gap:10px;font-size:14.5px;line-height:25.6px;font-family:'Raleway',sans-serif}
</style>
</head>
<body>

<!-- header -->
<div class="abs brand"><span class="brand-mark"></span>R W Builders</div>
<div class="abs topbar">
  <div class="item" style="left:54px">
    <svg width="26" height="26" viewBox="0 0 24 24" fill="none" stroke="#fff" stroke-width="1.4"><path d="M5 3h4l2 5-2.5 1.5a11 11 0 0 0 6 6L16 13l5 2v4a2 2 0 0 1-2 2A16 16 0 0 1 3 5a2 2 0 0 1 2-2z"/></svg>
    (555) 214-7730
  </div>
  <div class="sep"></div>
  <div class="item" style="left:276px">
    <svg width="28" height="22" viewBox="0 0 28 20" fill="none" stroke="#fff" stroke-width="1.4"><rect x="1" y="1" width="26" height="18"/><path d="M1 1l13 10L27 1"/></svg>
    office@rwbuilders.biz
  </div>
  <div class="social" style="left:594px" aria-label="Social link"></div>
  <div class="social" style="left:648px" aria-label="Social link"></div>
  <div class="social" style="left:702px" aria-label="Social link"></div>
</div>
<div class="abs nav" style="left:346px">Home</div>
<div class="abs nav" style="left:429px">About Us</div>
<div class="abs nav" style="left:535px">Services</div>
<div class="abs nav" style="left:634px">Protfolio</div>
<div class="abs nav" style="left:733px">Testimonials</div>
<div class="abs nav" style="left:861px">Contact Us</div>
<div class="btn login">Log In</div>

<!-- hero -->
<section class="abs hero" role="img" aria-label="Wheel loader and excavator on a construction site at sunset">
  <h1>An 8(A) Small<br>Business Prime<br>Contractor</h1>
  <div class="btn cta">Get Started</div>
  <span class="dot" style="left:572px;top:543px"></span>
  <span class="dot" style="left:593px;top:543px;background:var(--cyan)"></span>
  <span class="dot" style="left:614px;top:543px"></span>
</section>

<!-- services -->
<h2 class="section-title" style="top:833px">Our Services</h2>
<div class="tab on">Specialized Services</div>
<div class="tab off">General Contracting</div>

<svg class="abs" style="left:76px;top:1138px" width="16" height="28" viewBox="0 0 16 28" fill="none" stroke="#222" stroke-width="2"><path d="M14 2L2 14l12 12"/></svg>
<svg class="abs" style="left:1106px;top:1138px" width="16" height="28" viewBox="0 0 16 28" fill="none" stroke="#222" stroke-width="2"><path d="M2 2l12 12L2 26"/></svg>

<div class="card" style="left:111px">
  <div class="icon"><svg width="50" height="50" viewBox="0 0 50 50" fill="none" stroke="#fff" stroke-width="2"><path d="M10 46V10h20M10 16h24v6M18 10v36M6 46h38"/><rect x="26" y="28" width="14" height="18"/><path d="M30 33h6M30 39h6"/></svg></div>
  <h3>Site work</h3>
  <p>Lorem ipsum dolor sit amet, consectetur adipiscing elit, eiusmod magna aliqua.</p>
  <div class="more">Learn More →</div>
</div>
<div class="card active" style="left:360px">
  <div class="icon"><svg width="50" height="50" viewBox="0 0 50 50" fill="none" stroke="#1b3272" stroke-width="2"><rect x="6" y="28" width="38" height="16"/><path d="M6 36h38M18 28v8M32 28v8M12 36v8M25 36v8M38 36v8M30 22l10-14M36 6l6 4"/></svg></div>
  <h3>Concrete</h3>
  <p>Lorem ipsum dolor sit amet, consectetur adipiscing elit, eiusmod magna aliqua.</p>
  <div class="more">Learn More →</div>
</div>
<div class="card" style="left:608px">
  <div class="icon"><svg width="50" height="50" viewBox="0 0 50 50" fill="none" stroke="#fff" stroke-width="2"><rect x="14" y="6" width="22" height="40"/><path d="M19 12h4M27 12h4M19 19h4M27 19h4M19 26h4M27 26h4M19 33h4M27 33h4M22 46v-7h6v7M8 46h34"/></svg></div>
  <h3>General Building</h3>
  <p>Lorem ipsum dolor sit amet, consectetur adipiscing elit, eiusmod magna aliqua.</p>
  <div class="more">Learn More →</div>
</div>
<div class="card" style="left:857px">
  <div class="icon"><svg width="50" height="50" viewBox="0 0 50 50" fill="none" stroke="#fff" stroke-width="2"><rect x="6" y="8" width="38" height="26"/><path d="M14 24l11-9 11 9M18 22v8h14v-8M10 40h30M14 40v4M36 40v4"/></svg></div>
  <h3>Remodels</h3>
  <p>Lorem ipsum dolor sit amet, consectetur adipiscing elit, eiusmod magna aliqua.</p>
  <div class="more">Learn More →</div>
</div>

<!-- about -->
<section class="abs about">
  <h2>About Us</h2>
  <p>Lorem ipsum dolor sit amet, consectetur adipiscing elit, sed do eiusmod tempor incididunt ut labore et dolore magna aliqua. Ut enim ad minim veniam, quis nostrud exercitation ullamco laboris nisi ut aliquip ex ea commodo consequat. Duis aute irure dolor in reprehenderit in voluptate velit esse cillum dolore eu fugiat nulla pariatur. Excepteur sint occaecat cupidatat non proident, sunt in culpa qui officia deserunt mollit anim id est laborum.</p>
  <div class="btn cta">Learn More</div>
</section>
<div class="abs about-photo" role="img" aria-label="Yellow excavator dumping soil onto a dirt mound under a cloudy sky"></div>

<!-- testimonials -->
<h2 class="section-title" style="top:1965px">Our Testimonials</h2>
<div class="quote" style="left:111px"><span>“</span></div>
<div class="quote" style="left:648px"><span>“</span></div>
<p class="testi" style="left:173px">Lorem ipsum dolor sit amet, consectetur adipiscing elit, sed do eiusmod tempor incididunt ut labore et dolore magna aliqua. Ut enim ad minim veniam, quis nostrud exercitation ullamco laboris nisi ut aliquip ex ea commodo consequat. Duis aute irure dolor in fugiat nulla pariatur. Excepteur sint occaecat cupidatat non proident, sunt in culpa qui officia deserunt mollit anim id est laborum.</p>
<p class="testi" style="left:711px">Lorem ipsum dolor sit amet, consectetur adipiscing elit, sed do eiusmod tempor incididunt ut labore et dolore magna aliqua. Ut enim ad minim veniam, quis nostrud exercitation ullamco laboris nisi ut aliquip ex ea commodo consequat. Duis aute irure dolor in fugiat nulla pariatur. Excepteur sint occaecat cupidatat non proident, sunt in culpa qui officia deserunt mollit anim id est laborum.</p>
<div class="avatar" style="left:174px" role="img" aria-label="Portrait of client in suit"></div>
<div class="who" style="left:282px">- Mark Ellison</div>
<div class="avatar" style="left:711px" role="img" aria-label="Portrait of client"></div>
<div class="who" style="left:819px">- Mark Ellison</div>
<span class="gdot" style="left:572px"></span>
<span class="gdot" style="left:593px;background:var(--cyan)"></span>
<span class="gdot" style="left:614px"></span>

<!-- projects -->
<section class="abs projects">
  <h2 class="section-title" style="top:68px;color:var(--white)">Our Projects</h2>
  <div class="tile feature" style="left:111px;top:158px;width:476px;height:326px">
    <h4>Job Order Contract<br>County of Harbor Ridge</h4>
    <p>Harbor Ridge, CA | Task Orders Awarded: 155<br>Total Awarded Value: $20,000,000+</p>
  </div>
  <div class="tile" style="left:611px;top:158px;width:478px;height:326px;background:linear-gradient(135deg,#c9c4b4,#8a8f7a 50%,#c7d83c)" role="img" aria-label="Two engineers in hard hats reviewing building plans"></div>
  <div class="tile" style="left:111px;top:512px;width:308px;height:252px;background:linear-gradient(135deg,#a4704a,#c98a55 50%,#6b4a34)" role="img" aria-label="Desk with blueprints, laptop, gloves and hard hats seen from above"></div>
  <div class="tile" style="left:447px;top:512px;width:307px;height:252px;background:linear-gradient(180deg,#e9a75a,#a3703f 55%,#3a2b22)" role="img" aria-label="Workers shaking hands beside an excavator at sunset"></div>
  <div class="tile" style="left:782px;top:512px;width:307px;height:252px;background:linear-gradient(135deg,#d99a5a,#8e6a4a 50%,#4a3a30)" role="img" aria-label="Wheel loader and excavator on a dusty work site"></div>
  <div class="btn" style="left:533px;top:797px;width:134px;height:51px">View All</div>
</section>

<!-- footer -->
<footer class="abs footer">
  <div class="abs" style="left:150px;top:148px;display:flex;align-items:center;gap:10px;font-family:'Oswald',sans-serif;font-weight:700;font-size:28px;text-transform:uppercase"><span style="width:22px;height:22px;background:var(--white)"></span>R W Builders</div>
  <div class="abs" style="left:390px;top:64px;width:1px;height:210px;background:#3a3a3a"></div>
  <h5 style="left:432px">Quick Links</h5>
  <ul style="left:432px"><li>Home</li><li>About Us</li><li>Services</li><li>Protfolio</li><li>Testimonials</li><li>Contact Us</li></ul>
  <h5 style="left:640px">Our Company</h5>
  <ul style="left:640px"><li>Terms &amp; conditions</li><li>Privacy Policy</li><li>About Us</li><li>Support</li></ul>
  <h5 style="left:864px">Contact us</h5>
  <div class="contact-row" style="top:104px"><svg width="14" height="20" viewBox="0 0 14 20"><path d="M7 0a7 7 0 0 1 7 7c0 5-7 13-7 13S0 12 0 7a7 7 0 0 1 7-7z" fill="#fff"/><circle cx="7" cy="7" r="2.6" fill="#1d1d1d"/></svg><span>P.O. Box 2481<br>Arroyo Vista, CA 93400</span></div>
  <div class="contact-row" style="top:170px"><svg width="16" height="16" viewBox="0 0 24 24"><path d="M5 2h4l2 5-2.5 1.5a11 11 0 0 0 6 6L16 12l5 2v4a2 2 0 0 1-2 2A16 16 0 0 1 3 4a2 2 0 0 1 2-2z" fill="#fff"/></svg><span>(555) 214-7730</span></div>
  <div class="contact-row" style="top:211px"><svg width="16" height="14" viewBox="0 0 16 12" style="margin-top:6px"><rect width="16" height="12" fill="#fff"/><path d="M0 0l8 6 8-6" stroke="#1d1d1d" fill="none"/></svg><span>office@rwbuilders.biz</span></div>
  <div class="abs" style="left:111px;top:305px;width:978px;height:1px;background:#3a3a3a"></div>
  <div class="abs" style="left:0;top:338px;width:1200px;text-align:center;font-size:14.5px;font-family:'Raleway',sans-serif">©Copyrights 2024 R W Builders &nbsp;| &nbsp; All Rights Reserved</div>
</footer>

</body>
</html>
```